Residential Remodeling Contractor needs updated business card

I need a new design for my business card.
Name of the company is Ridgefell Construction. I need a card that commands presence, strength, integrity. I have been in business for 28 years. I am a Residential Remodeling Contractor that covers all aspects of a residential remodel and build.

```html
<!DOCTYPE html>
<html lang="en">
<head>
<meta charset="utf-8">
<title>Ridgefell Construction – Business Card</title>
<link href="https://fonts.googleapis.com/css2?family=Noto+Serif:wght@700&family=Arimo:wght@400&display=swap" rel="stylesheet">
<style>
  :root {
    --backdrop: #9a9a9a;
    --navy: #1b3c80;
    --navy-deep: #1e3772;
    --card-white: #ffffff;
    --ink: #333333;
  }
  * { margin: 0; padding: 0; box-sizing: border-box; }
  html, body {
    width: 1200px; height: 1059px; overflow: hidden;
    background: var(--backdrop);
  }
  .canvas { position: relative; width: 1200px; height: 1059px; }

  .card {
    position: absolute;
    width: 689px; height: 391px;
    border-radius: 16px;
    overflow: hidden;
  }
  .card--front { left: 256px; top: 89px; background: var(--card-white); }
  .card--back  { left: 254px; top: 569px; }

  .company {
    position: absolute;
    display: flex; align-items: center;
    font-family: "Arimo", Arial, sans-serif;
    font-weight: 400;
    white-space: nowrap;
    color: var(--navy);
  }
  .company__mark { flex: none; background: var(--navy); }
  .card--front .company {
    left: 34px; top: 92px; gap: 12px;
    font-size: 30px;
  }
  .card--front .company__mark { width: 26px; height: 26px; }

  .holder {
    position: absolute; right: 34px; top: 168px; text-align: right;
  }
  .holder__name {
    font-family: "Noto Serif", Georgia, serif;
    font-weight: 700; font-size: 28px; line-height: 1;
    color: var(--navy); letter-spacing: 0.2px;
  }
  .holder__title {
    font-family: "Arimo", Arial, sans-serif;
    font-size: 17px; color: var(--ink); margin-top: 2px;
  }
  .rule {
    position: absolute; left: 34px; top: 206px;
    width: 472px; height: 1px; background: var(--navy);
  }
  .edge-tab {
    position: absolute; left: 669px; top: 172px;
    width: 20px; height: 43px;
    background: var(--navy); border-radius: 4px 0 0 4px;
  }

  .details {
    position: absolute; left: 34px; top: 223px;
    font-family: "Arimo", Arial, sans-serif;
    font-size: 17.5px; color: var(--ink);
  }
  .details__address { line-height: 22px; margin-bottom: 13px; }
  .details__line {
    display: flex; align-items: center; gap: 7px;
    height: 27px;
  }
  .details__line svg { width: 12px; height: 12px; fill: var(--navy); flex: none; }

  .back-field {
    position: absolute; inset: 0;
    background:
      radial-gradient(ellipse 70% 80% at 100% 10%, rgba(120,150,210,0.75), rgba(120,150,210,0) 70%),
      linear-gradient(90deg, var(--navy-deep), #24407f);
  }
  .card--back .company {
    left: 448px; top: 283px; gap: 9px;
    font-size: 20px; color: var(--card-white);
  }
  .card--back .company__mark { width: 18px; height: 18px; background: var(--card-white); }
</style>
</head>
<body>
<div class="canvas">

  <section class="card card--front">
    <div class="company"><span class="company__mark"></span>Ridgefell Construction</div>

    <div class="holder">
      <div class="holder__name">DANIEL OKAFOR</div>
      <div class="holder__title">Owner &amp; Manager</div>
    </div>
    <div class="rule"></div>
    <div class="edge-tab"></div>

    <div class="details">
      <p class="details__address">P.O. Box&nbsp; Street Name<br>Country Name AB, A5B 521</p>
      <p class="details__line">
        <svg viewBox="0 0 12 12"><path d="M1 4c0-2 10-2 10 0v1.5H8.5V4.5h-5v1H1zM3 6h6l2 4.5H1z"/></svg>
        555 214 7390
      </p>
      <p class="details__line">
        <svg viewBox="0 0 12 12"><path d="M1 5l5-4 5 4v6H1z M2 5.4l4 3 4-3" stroke="#fff" stroke-width="0.8"/></svg>
        info@ridgefellconstruction.com
      </p>
      <p class="details__line">
        <svg viewBox="0 0 12 12"><circle cx="6" cy="6" r="5.5"/><path d="M3 3.5c1.5 0 2 1 1.5 2s1 1.5.5 3M7.5 1.5c0 1.5 1.5 1.5 2.5 2.5" stroke="#fff" stroke-width="1" fill="none"/></svg>
        www.ridgefellconstruction.com
      </p>
    </div>
  </section>

  <section class="card card--back">
    <div class="back-field" role="img" aria-label="Repeating pattern of brand symbols on a navy field, fading lighter toward the upper right"></div>
    <div class="company"><span class="company__mark"></span>Ridgefell Construction</div>
  </section>

</div>
</body>
</html>
```